Bright Harbor Design

We need a web design for our startup company based in Zurich, Switzerland called Bright Harbor. We offer professional flirt and dating advice, self development with seminars and practical coachings.

The final website aims for two capital goals. First, it will contain text, pictures and video based content presenting and advertising our services. Furthermore, we want to bind our costumers with a plattform offering them to share their expiriences related with our services.

The targeted group will be men from 25 to 40 years.
Updates

The design requires also a register-box to put in the clients Name and Email

I need (besides of the "email registration box") a "Video Gallery", "Blog" and "Agenda (with the next events to come)"

Reason: I want to make a poll now

Target Market(s)

Guys around 25 to 40 years who want to improve their social lifestyle

Industry/Entity Type

Advertising

Requirements
Must have
• First and foremost, the design must transfer strong emotions and suggest an attractive social lifestyle.

The design should not be overloaded with content but should include pictures, videos and text.

The design should present a modern, urban lifestyle.
Nice to have
• There is a logo attached to the assignement. However, if you have a good idea for an improved or different logo, please do not hesitate to design your ideas.

```html
<!DOCTYPE html>
<html lang="en">
<head>
<meta charset="utf-8">
<title>Bright Harbor</title>
<link href="https://fonts.googleapis.com/css2?family=Open+Sans:wght@400;600;700&family=PT+Sans+Narrow:wght@400;700&display=swap" rel="stylesheet">
<style>
:root{
  --navy:#13254a;
  --navy-deep:#0e1d3c;
  --blue:#2f6fae;
  --blue-light:#4a8cc8;
  --heading:#1d4f86;
  --link:#2a6cb0;
  --red:#c8202b;
  --orange:#f5a600;
  --text:#4a4a4a;
  --gray-bg:#e9e9e9;
  --sidebar:#efefef;
  --footer:#eeeff1;
  --white:#ffffff;
}
*{margin:0;padding:0;box-sizing:border-box}
html,body{width:926px;height:1200px;overflow:hidden}
body{position:relative;background:linear-gradient(#e4e4e4 0,#e4e4e4 472px,#f4f4f4 600px);font-family:"Open Sans",Arial,sans-serif;color:var(--text)}
.abs{position:absolute}
.hero-band{left:0;top:0;width:926px;height:378px;background:radial-gradient(ellipse at 60% 40%,#3f82c2 0,#2c69a7 55%,#1f5289 100%)}
.top-bar{left:0;top:0;width:926px;height:54px;background:linear-gradient(#0f2046,#1a3466);border-bottom:1px solid #4f86c2}
.logo-box{left:98px;top:0;width:220px;height:84px;background:var(--white);border-radius:0 0 6px 6px;box-shadow:0 2px 6px rgba(0,0,0,.35);display:flex;align-items:center;justify-content:center;gap:10px}
.logo-mark{width:22px;height:22px;border-radius:50%;background:var(--navy)}
.logo-name{font-family:"Open Sans",sans-serif;font-weight:700;font-size:19px;color:var(--navy)}
.util{top:19px;font-size:9px;color:#fff;display:flex;align-items:center;gap:5px}
.util svg{width:9px;height:9px}
.search-input{left:578px;top:17px;width:182px;height:17px;background:#fff;font-size:8.5px;color:#999;padding:3px 6px}
.search-btn{left:760px;top:17px;width:48px;height:17px;background:var(--navy);color:#fff;font-size:8.5px;text-align:center;line-height:17px}
.nav{top:61px;height:24px;font-size:9.5px;color:#fff;line-height:24px}
.nav-item{position:absolute;top:0;transform:translateX(-50%);white-space:nowrap}
.nav-sep{position:absolute;top:-6px;width:1px;height:36px;background:rgba(255,255,255,.15)}
.nav-home{position:absolute;left:419px;top:0;width:59px;height:24px;background:var(--navy-deep);border-radius:2px}
.hero-photo{left:102px;top:103px;width:431px;height:243px;border:3px solid #fff;background:linear-gradient(120deg,#7a6f66,#3a3a40 45%,#b7b0a6 75%,#5c4c44)}
.arrow{width:44px;height:44px;border-radius:50%;background:radial-gradient(circle at 50% 40%,#2d5d96,#142f5a);border:2px solid rgba(255,255,255,.2);top:186px}
.arrow svg{position:absolute;left:14px;top:13px}
.hero-title{left:558px;top:112px;font-family:"Open Sans",sans-serif;font-size:14.5px;color:#fff;letter-spacing:.1px}
.hero-rule{left:558px;top:140px;width:248px;height:1px;background:rgba(255,255,255,.35)}
.hero-text{left:556px;top:155px;width:264px;font-size:9.6px;line-height:16.2px;color:#e3eefa}
.join{left:567px;top:264px;width:123px;height:30px;border-radius:15px;background:linear-gradient(#ffc21a,#f29300);box-shadow:0 1px 2px rgba(0,0,0,.3);color:#fff;font-size:12.5px;display:flex;align-items:center;padding-left:10px;gap:8px}
.join-dot{width:17px;height:17px;border-radius:50%;background:#d88300;position:relative}
.join-dot:after{content:"";position:absolute;left:6px;top:4.5px;border-left:6px solid #ffd04d;border-top:4px solid transparent;border-bottom:4px solid transparent}
.join-reflect{left:567px;top:300px;width:123px;height:22px;border-radius:15px 15px 0 0;background:linear-gradient(rgba(245,166,0,.45),rgba(245,166,0,0))}
.main-panel{left:98px;top:378px;width:500px;height:674px;background:#fff;border-left:1px solid #ddd}
.sidebar{left:598px;top:378px;width:228px;height:674px;background:var(--sidebar);border-right:1px solid #ccc}
.h-section{font-family:"PT Sans Narrow",sans-serif;font-weight:700;color:var(--heading);font-size:16.5px;text-transform:uppercase;letter-spacing:-.1px}
.lead{left:120px;top:426px;font-size:9px;font-weight:700;color:#222}
.body-copy{font-size:8.3px;line-height:14px;color:#555}
.btn-blue{background:var(--heading);color:#fff;font-family:"PT Sans Narrow",sans-serif;font-weight:700;font-size:11px;text-align:center;line-height:25px;height:25px}
.btn-orange{background:var(--orange);color:#fff;font-family:"PT Sans Narrow",sans-serif;font-weight:700;font-size:11px;text-align:center;line-height:25px;height:25px}
.video-main{left:114px;top:568px;width:236px;height:113px;border:2px solid var(--heading);background:linear-gradient(110deg,#3a2a20,#8a5a32 40%,#c89a5a 60%,#5a3030)}
.video-thumb{top:693px;width:72px;height:61px;border:2px solid var(--heading)}
.play{position:absolute;left:50%;top:50%;transform:translate(-50%,-50%);background:#1a1a1a;border-radius:3px}
.play:after{content:"";position:absolute;border-left-color:#fff;border-left-style:solid;border-top:solid transparent;border-bottom:solid transparent}
.play-lg{width:36px;height:26px}
.play-lg:after{left:14px;top:7px;border-left-width:11px;border-top-width:6px;border-bottom-width:6px}
.play-sm{width:18px;height:15px}
.play-sm:after{left:7px;top:4px;border-left-width:6px;border-top-width:3.5px;border-bottom-width:3.5px}
.more{font-size:8.5px;color:var(--link)}
.rule{height:1px;background:#e4e4e4}
.tip-img{left:115px;width:55px;height:45px;border:2px solid var(--heading)}
.tip-text{left:178px;width:145px}
.click{font-size:8.3px;color:var(--link)}
.news-date{left:374px;font-size:8.3px;color:var(--link)}
.news-text{left:374px;width:204px}
.side-head{left:598px;width:245px;height:31px;background:var(--navy);color:#fff;font-family:"PT Sans Narrow",sans-serif;font-weight:700;font-size:16.5px;padding-left:16px;line-height:31px}
.side-fold{left:826px;width:0;height:0;border-top:8px solid #0a1630;border-right:17px solid transparent}
.blog-img{left:605px;width:96px;height:64px;border:1px solid #bbb;padding:2px;background:#fff}
.blog-img div{width:100%;height:100%}
.blog-title{left:708px;font-size:9.6px;color:var(--red)}
.blog-date{left:708px;font-size:8px;color:#555}
.blog-text{left:708px;width:110px;font-size:8px;line-height:12.3px;color:#666;text-align:justify}
.member{width:58px;height:57px;border-radius:6px;border:1px solid #ccc}
.news-input{left:614px;top:986px;width:200px;height:25px;background:#fff;border:1px solid #c9c9c9;box-shadow:inset 0 1px 2px rgba(0,0,0,.12);font-size:8px;font-style:italic;color:#777;padding:7px 12px}
.footer{left:0;top:1052px;width:926px;height:148px;background:var(--footer);border-top:1px solid #ddd}
.sitemap-title{left:120px;top:1063px;font-size:9.5px;color:#333}
.fl{font-size:8.2px;color:#555}
.fl:before{content:"›";margin-right:8px;color:#333}
.social{top:1078px;width:16px;height:16px;border-radius:2px}
.copy{right:100px;top:1108px;font-size:8.2px;color:#333}
</style>
</head>
<body>
<div class="abs hero-band"></div>
<div class="abs top-bar"></div>

<div class="abs logo-box"><span class="logo-mark"></span><span class="logo-name">Bright Harbor</span></div>

<div class="abs util" style="left:450px"><svg viewBox="0 0 10 10"><rect x="2" y="4" width="6" height="6" fill="#ccd"/><path d="M3 4V3a2 2 0 0 1 4 0v1" stroke="#ccd" fill="none"/></svg>Login</div>
<div class="abs util" style="left:506px"><svg viewBox="0 0 10 10"><rect x="1" y="2" width="7" height="7" fill="none" stroke="#ccd"/><path d="M4 6l5-5" stroke="#ccd"/></svg>Register</div>
<div class="abs search-input">type your word here</div>
<div class="abs search-btn">SEARCH</div>

<div class="abs nav" style="left:0;width:926px">
  <div class="nav-home"></div>
  <span class="nav-item" style="left:449px">Home</span>
  <span class="nav-item" style="left:510px">About us</span>
  <span class="nav-sep" style="left:542px"></span>
  <span class="nav-item" style="left:571px">Advise</span>
  <span class="nav-sep" style="left:599px"></span>
  <span class="nav-item" style="left:626px">Dating</span>
  <span class="nav-sep" style="left:654px"></span>
  <span class="nav-item" style="left:690px">Dating Tips</span>
  <span class="nav-sep" style="left:726px"></span>
  <span class="nav-item" style="left:748px">Blog</span>
  <span class="nav-sep" style="left:770px"></span>
  <span class="nav-item" style="left:799px">Contact</span>
</div>

<div class="abs hero-photo" role="img" aria-label="Photo of a man and a woman meeting and smiling on a busy city street"></div>
<div class="abs arrow" style="left:26px"><svg width="12" height="14" viewBox="0 0 12 14"><path d="M9 2L3 7l6 5" stroke="#fff" stroke-width="2.5" fill="none"/></svg></div>
<div class="abs arrow" style="left:844px"><svg width="12" height="14" viewBox="0 0 12 14"><path d="M3 2l6 5-6 5" stroke="#fff" stroke-width="2.5" fill="none"/></svg></div>

<div class="abs hero-title">LOREM IPSUM DOLOR SIT AMET, ELIT</div>
<div class="abs hero-rule"></div>
<p class="abs hero-text">Cum sociis natoque penatibus et magnis dis parturient montes, nascetur ridiculus mus. In iaculis facilisis massa. Etiam eu urna. Sed porta.Cum sociis natoque penatibus et magnis dis parturient montes, nascetur ridiculus mus. In iaculis facilisis massa. Etiam eu urna. Sed porta.</p>
<div class="abs join"><span class="join-dot"></span>JOIN NOW</div>
<div class="abs join-reflect"></div>

<div class="abs main-panel"></div>
<div class="abs sidebar"></div>

<h1 class="abs h-section" style="left:120px;top:394px">Welcome to Bright Harbor</h1>
<p class="abs lead">Mauris vel lacus vitae felis vestibulum volutpat. Etiam est nunc, venisl.</p>
<p class="abs body-copy" style="left:121px;top:443px;width:440px">Sed ut perspiciatis unde omnis iste natus error sit voluptatem accusantium doloremque laudantium, totam rem aperiam, eaque ipsa quae ab illo inventore veritatis et quasi architecto beatae vitae dicta sunt explicabo. Nemo enim ipsam voluptatem quia voluptas sit aspernatur aut odit aut fugit, sed quia consequuntur magni dolores eos qui ratione voluptatem sequi nesciunt. Neque porro quisquam est, qui dolorem ipsum quia dolor sit amet.</p>
<div class="abs btn-blue" style="left:496px;top:511px;width:62px">learn more</div>

<h2 class="abs h-section" style="left:114px;top:537px">Our Videos</h2>
<div class="abs video-main" role="img" aria-label="Video still of a couple browsing in a warmly lit shop"><span class="play play-lg"></span></div>
<div class="abs video-thumb" style="left:114px;background:linear-gradient(#e8e4dc,#6a6a70)" role="img" aria-label="Video still of a couple walking"><span class="play play-sm"></span></div>
<div class="abs video-thumb" style="left:196px;background:linear-gradient(#6a5a50,#c8b8a8)" role="img" aria-label="Video still of friends at a party"><span class="play play-sm"></span></div>
<div class="abs video-thumb" style="left:278px;background:linear-gradient(#a08070,#4a4040)" role="img" aria-label="Video still of a smiling couple"><span class="play play-sm"></span></div>
<p class="abs body-copy" style="left:362px;top:567px;width:200px;text-align:justify">Sed ut perspiciatis unde omnis iste natus error sit voluptatem accusantium doloremque laudantium, totam rem aperiam, eaque ipsa quae ab illo inventore veritatis et quasi architecto beatae vitae dicta sunt explicabo. Nemo enim ipsam voluptatem quia voluptas sit aspernatur aut odit aut fugit, sed quia consequuntur magni dolores eos qui ratione voluptatem sequi nesciunt. Neque porro quisquam est, qui dolorem ipsum quia dolor sit amet.</p>
<span class="abs more" style="left:525px;top:716px">More &gt;&gt;</span>

<h2 class="abs h-section" style="left:114px;top:796px">Dating Tips</h2>
<div class="abs rule" style="left:114px;top:822px;width:198px"></div>
<div class="abs tip-img" style="top:834px;background:linear-gradient(#b89a70,#6a8a50)" role="img" aria-label="Photo of a couple lying in the grass"></div>
<p class="abs body-copy tip-text" style="top:833px;line-height:12.4px">Sed ut perspiciatis unde omnis iste natus error sit voluptatem accusantium doloremque laudantium.<br><span class="click">Click Here &gt;&gt;</span></p>
<div class="abs tip-img" style="top:896px;background:linear-gradient(#7a5a40,#3a5a30)" role="img" aria-label="Photo of a couple close together outdoors"></div>
<p class="abs body-copy tip-text" style="top:895px;line-height:12.4px">Sed ut perspiciatis unde omnis iste natus error sit voluptatem accusantium doloremque laudantium.<br><span class="click">Click Here &gt;&gt;</span></p>
<div class="abs tip-img" style="top:958px;background:linear-gradient(90deg,#d8d0c8,#8a7060,#e8e0d8)" role="img" aria-label="Photo of a couple facing each other"></div>
<p class="abs body-copy tip-text" style="top:957px;line-height:12.4px">Sed ut perspiciatis unde omnis iste natus error sit voluptatem accusantium doloremque laudantium.<br><span class="click">Click Here &gt;&gt;</span></p>
<span class="abs more" style="left:285px;top:1025px">More &gt;&gt;</span>

<h2 class="abs h-section" style="left:370px;top:799px">News</h2>
<div class="abs rule" style="left:370px;top:822px;width:198px"></div>
<span class="abs news-date" style="top:835px">Mar 12, 2013</span>
<p class="abs body-copy news-text" style="top:846px;line-height:12.4px">Sed ut perspiciatis unde omnis iste natus error sit voluptatem accusantium doloremque laudantium, totam rem aperiam, eaque ipsa quae ab illo inven.</p>
<span class="abs news-date" style="top:896px">Mar 12, 2013</span>
<p class="abs body-copy news-text" style="top:907px;line-height:12.4px">Sed ut perspiciatis unde omnis iste natus error sit voluptatem accusantium doloremque laudantium, totam rem aperiam, eaque ipsa quae ab illo inven.</p>
<span class="abs news-date" style="top:966px">Mar 12, 2013</span>
<p class="abs body-copy news-text" style="top:977px;line-height:12.4px">Sed ut perspiciatis unde omnis iste natus error sit voluptatem accusantium doloremque laudantium, totam rem aperiam, eaque ipsa quae ab illo inven.</p>
<span class="abs more" style="left:525px;top:1025px">More &gt;&gt;</span>

<div class="abs side-head" style="top:378px">Latest Blog</div>
<div class="abs side-fold" style="top:409px"></div>
<div class="abs blog-img" style="top:423px" role="img" aria-label="Photo of a couple kissing outdoors"><div style="background:linear-gradient(#5a7a50,#3a3030)"></div></div>
<span class="abs blog-title" style="top:417px">Excepteur sint occaecat.</span>
<span class="abs blog-date" style="top:432px">mar 12, 2013</span>
<p class="abs blog-text" style="top:444px">Sed ut perspiciatis unde omnis iste natus error sit voluptatem accusantium doloremque laudantium.</p>
<div class="abs blog-img" style="top:516px" role="img" aria-label="Photo of a couple sharing a drink"><div style="background:linear-gradient(120deg,#2a1a14,#8a5a40,#2a1a14)"></div></div>
<span class="abs blog-title" style="top:510px">Excepteur sint occaecat.</span>
<span class="abs blog-date" style="top:525px">mar 12, 2013</span>
<p class="abs blog-text" style="top:537px">Sed ut perspiciatis unde omnis iste natus error sit voluptatem accusantium doloremque laudantium.</p>
<div class="abs blog-img" style="top:609px" role="img" aria-label="Illustration of two small figures holding a heart balloon"><div style="background:linear-gradient(#f2f0f4,#e2dde6)"></div></div>
<span class="abs blog-title" style="top:603px">Excepteur sint occaecat.</span>
<span class="abs blog-date" style="top:618px">mar 12, 2013</span>
<p class="abs blog-text" style="top:630px">Sed ut perspiciatis unde omnis iste natus error sit voluptatem accusantium doloremque laudantium.</p>
<div class="abs btn-blue" style="left:750px;top:689px;width:63px">learn more</div>

<div class="abs side-head" style="top:735px;background:linear-gradient(90deg,#3c5d8e,#5a7aa8)" role="img" aria-label="Members header with a heart pattern">Members</div>
<div class="abs side-fold" style="top:766px"></div>
<div class="abs member" style="left:611px;top:775px;background:linear-gradient(#d8d8dc,#7a7a80)" role="img" aria-label="Member portrait"></div>
<div class="abs member" style="left:682px;top:775px;background:linear-gradient(#c8b890,#5a4a3a)" role="img" aria-label="Member portrait"></div>
<div class="abs member" style="left:752px;top:775px;background:linear-gradient(#7a3a6a,#3a2030)" role="img" aria-label="Member portrait"></div>
<div class="abs member" style="left:611px;top:846px;background:linear-gradient(#e8e2dc,#8a6a50)" role="img" aria-label="Member portrait"></div>
<div class="abs member" style="left:682px;top:846px;background:linear-gradient(#d89a80,#8a4a3a)" role="img" aria-label="Member portrait"></div>
<div class="abs member" style="left:752px;top:846px;background:linear-gradient(#e8d090,#b08a60)" role="img" aria-label="Member portrait"></div>
<div class="abs btn-orange" style="left:750px;top:914px;width:63px">learn more</div>

<div class="abs side-head" style="top:949px">Newsletter</div>
<div class="abs side-fold" style="top:980px"></div>
<div class="abs news-input">Your Email Id</div>
<div class="abs btn-orange" style="left:733px;top:1019px;width:80px;font-size:11.5px">Subscribe</div>

<div class="abs footer"></div>
<span class="abs sitemap-title">Sitemap</span>
<span class="abs fl" style="left:119px;top:1088px">Home</span>
<span class="abs fl" style="left:119px;top:1107px">About Us</span>
<span class="abs fl" style="left:119px;top:1125px">Dating</span>
<span class="abs fl" style="left:119px;top:1143px">Dating Tips</span>
<span class="abs fl" style="left:119px;top:1162px">Blog</span>
<span class="abs fl" style="left:235px;top:1088px">FAQ</span>
<span class="abs fl" style="left:235px;top:1107px">Sitemap</span>
<span class="abs fl" style="left:235px;top:1125px">Disclaimer</span>
<span class="abs fl" style="left:235px;top:1143px">Terms of Use</span>
<span class="abs fl" style="left:235px;top:1162px">Privacy Policy</span>
<span class="abs fl" style="left:360px;top:1088px">Blog</span>
<span class="abs fl" style="left:360px;top:1107px">Blog Archive</span>
<span class="abs fl" style="left:360px;top:1125px">Compatible Partners</span>
<span class="abs fl" style="left:360px;top:1143px">International Dating</span>
<span class="abs social" style="left:746px;background:#3b5a98"></span>
<span class="abs social" style="left:768px;background:#3aa8dc"></span>
<span class="abs social" style="left:789px;background:#f08a24"></span>
<span class="abs social" style="left:809px;background:#1f6ea8"></span>
<span class="abs copy">© 2013 Bright Harbor, All Rights Reserved</span>
</body>
</html>
```